RW Framewell Inc Business cards

We need business cards using our existing logo but slightly modified. Right now the logo says RW Loadbearing Masonry. We want to keep the RW part of the design, but replace the Structural Concrete portion with "FRAMEWELL". Please see the attached file.
Ideally this would be a blank template so we can add Different Names, titles, and phone numbers later.
On the one side we want only the logo and on the other side the detail. I'm attaching an example for you to see.
Please reach out with any other questions. Our address and other details will be given out once we find a design we like.

Target Market(s)

Construction Industry

```html
<!DOCTYPE html>
<html lang="en">
<head>
<meta charset="utf-8">
<title>RW Framewell Inc – Business Cards</title>
<link rel="stylesheet" href="https://fonts.googleapis.com/css2?family=Montserrat:wght@700&family=Roboto:wght@400;500&family=Ubuntu:wght@700&display=swap">
<style>
  :root {
    --backdrop: #5a80bb;
    --brand-blue: #2d5ea5;
    --card-back: #2f5e9f;
    --card-back-mark: #4677bd;
    --card-front: #ffffff;
    --text-grey: #5f6166;
    --accent-grey: #6a6a6a;
    --rule-blue: #3a6bb0;
  }
  * { box-sizing: border-box; margin: 0; padding: 0; }
  html, body {
    width: 1200px; height: 852px; overflow: hidden;
    background: var(--backdrop);
  }
  .card-set {
    width: 1200px; height: 852px;
    display: flex; align-items: center; justify-content: center; gap: 44px;
  }
  .card {
    width: 520px; height: 300px;
    border-radius: 22px;
    position: relative;
    box-shadow: 0 6px 18px rgba(20, 40, 80, 0.25);
  }
  .card--back {
    background: var(--card-back);
    display: flex; align-items: center; justify-content: center;
  }
  .card--front {
    background: var(--card-front);
    padding: 44px 40px 0;
  }
  .wordmark {
    display: flex; align-items: center; justify-content: center; gap: 12px;
    font-family: "Montserrat", sans-serif; font-weight: 700;
    letter-spacing: 2px; white-space: nowrap;
  }
  .wordmark__square {
    width: 16px; height: 16px; background: var(--accent-grey);
  }
  .card--back .wordmark { font-size: 46px; color: var(--card-back-mark); }
  .card--back .wordmark__square { width: 20px; height: 20px; background: var(--card-back-mark); }
  .card--front .wordmark { font-size: 38px; color: var(--brand-blue); }

  .details {
    display: flex; justify-content: center; gap: 30px;
    margin-top: 48px;
    font-family: "Roboto", sans-serif; color: var(--text-grey);
  }
  .person { text-align: right; }
  .person__name {
    font-family: "Ubuntu", sans-serif; font-weight: 700;
    font-size: 19px; color: var(--brand-blue);
  }
  .person__title { font-size: 13px; margin-top: 2px; }
  .person__rule { border: 0; border-top: 1.5px solid var(--rule-blue); margin: 7px 0 6px; }
  .person__address { font-size: 13px; line-height: 1.35; font-style: normal; }
  .contact { list-style: none; font-size: 13px; padding-top: 2px; }
  .contact li { display: flex; align-items: center; gap: 10px; height: 21px; }
  .contact svg { width: 12px; height: 12px; fill: var(--brand-blue); flex: none; }
</style>
</head>
<body>
<main class="card-set">
  <section class="card card--back" aria-label="Card back">
    <div class="wordmark"><span class="wordmark__square"></span><span>RW FRAMEWELL</span></div>
  </section>

  <section class="card card--front" aria-label="Card front">
    <div class="wordmark"><span class="wordmark__square"></span><span>RW FRAMEWELL</span></div>
    <div class="details">
      <div class="person">
        <p class="person__name">Daniel Reyes</p>
        <p class="person__title">Managing Director</p>
        <hr class="person__rule">
        <address class="person__address">18 Timber Row, Millbrook,<br>Oregon, US 97000</address>
      </div>
      <ul class="contact">
        <li>
          <svg viewBox="0 0 12 12" aria-hidden="true"><path d="M2.5 1h2l1 2.5-1.3 1a6 6 0 0 0 2.3 2.3l1-1.3L11 6.5v2c0 .8-.7 1.5-1.5 1.5A8.5 8.5 0 0 1 1 2.5C1 1.7 1.7 1 2.5 1z"/></svg>
          <span>555-010-2040</span>
        </li>
        <li>
          <svg viewBox="0 0 12 12" aria-hidden="true"><path d="M1 2.5h10v7H1z M1.6 3l4.4 3.4L10.4 3" stroke="#fff" stroke-width="1"/></svg>
          <span>daniel@framewell-mail.com</span>
        </li>
        <li>
          <svg viewBox="0 0 12 12" aria-hidden="true"><circle cx="6" cy="6" r="5"/><path d="M1 6h10M6 1c-2.5 3-2.5 7 0 10M6 1c2.5 3 2.5 7 0 10" stroke="#fff" stroke-width="0.8" fill="none"/></svg>
          <span>www.framewell-mail.com</span>
        </li>
      </ul>
    </div>
  </section>
</main>
</body>
</html>
```